Cover Art Design for a Notebook

We are going to give away some note books to our marketing department and want an elegant art design for the cover. There is a theme centered around ABCD of marketing that we want to leverage in the design. So these letters should be prominent in the design. The ABCD stand for Agility, Boost, Customer, Data.

If you could Cleverly incorporate these words into the letters with a good design that would be good.

But please make the ABCD the focus of the artwork. The words associated with them should be subtle, in the background, visible but not the focus.

We are looking for stylish. We want people to feel proud of the ELEGANT DESIGN when they take out this notebook for business.

Also worth mentioning- We are a biotechnology company so if you incorporate elements in that theme in, on, or around the ABCD letters, it could be a good idea. As long as it doesn’t kill the rest of the design.

I will upload our logo for Kelvara Biolume Sciences later (you can see it online) and this will need to go in one corner.

Notebook will be A5 format. Image on front cover only. Need ASAP.

(Do not make baby blocks as we don’t want something that looks like a kids book)

Target Market(s)

business people who feel proud to pull out this notebook

Industry/Entity Type

Biotechnology

Colors
ec1f27
ffffff
000000

Requirements
Must have
• ELEGANT ART DESIGN USING ABCD
Nice to have
• see brief above
Should not have
• baby blocks

```html
<!DOCTYPE html>
<html lang="en">
<head>
<meta charset="utf-8">
<title>ABCD of Marketing – Notebook Cover</title>
<link rel="stylesheet" href="https://fonts.googleapis.com/css2?family=Arimo:wght@400;700&display=swap">
<style>
  :root {
    --brand-red: #ec1f27;
    --ink: #222222;
    --frame: #ffffff;
    --mint-pale: #e9fcef;
    --mint: #86f7ad;
    --mint-bright: #3df479;
    --mint-soft: #b9f6cd;
    --motif: rgba(255, 255, 255, 0.35);
  }
  html, body {
    margin: 0;
    padding: 0;
    width: 846px;
    height: 1200px;
    overflow: hidden;
    background: #ffffff;
  }
  .cover {
    position: relative;
    width: 846px;
    height: 1200px;
    overflow: hidden;
    font-family: "Arimo", Arial, sans-serif;
    background:
      radial-gradient(ellipse 60% 45% at 100% 20%, var(--mint-bright) 0%, rgba(61,244,121,0) 100%),
      linear-gradient(160deg, var(--mint-pale) 0%, var(--mint) 45%, var(--mint) 70%, var(--mint-soft) 100%);
  }
  .cover svg {
    position: absolute;
    inset: 0;
    width: 846px;
    height: 1200px;
  }
  .hex-frame {
    fill: none;
    stroke: var(--frame);
    stroke-width: 3.5;
  }
  .connector {
    stroke: var(--frame);
    stroke-width: 3.5;
  }
  .initial {
    fill: var(--brand-red);
    font-size: 158px;
    font-weight: 400;
    text-anchor: middle;
  }
  .keyword {
    fill: var(--ink);
    font-size: 45px;
    font-weight: 400;
    text-anchor: middle;
    letter-spacing: -0.5px;
  }
  .brand-name {
    fill: var(--brand-red);
    font-size: 36px;
    font-weight: 700;
    letter-spacing: -1px;
  }
  .motif {
    fill: var(--motif);
  }
</style>
</head>
<body>
<main class="cover">
  <svg viewBox="0 0 846 1200" xmlns="http://www.w3.org/2000/svg">
    <g class="brand">
      <text class="brand-name" x="73" y="132">Kelvara Biolume</text>
      <text class="brand-name" x="73" y="170">Sciences</text>
    </g>

    <g class="science-motifs">
      <ellipse class="motif" role="img" aria-label="Faint magnet icon" cx="677" cy="324" rx="33" ry="44"/>
      <ellipse class="motif" role="img" aria-label="Faint chromosome icon" cx="483" cy="428" rx="36" ry="36"/>
      <ellipse class="motif" role="img" aria-label="Faint lab flask icon" cx="760" cy="770" rx="44" ry="62"/>
      <ellipse class="motif" role="img" aria-label="Faint chromosome icon" cx="280" cy="1002" rx="58" ry="32"/>
      <ellipse class="motif" role="img" aria-label="Faint atom icon" cx="689" cy="1030" rx="72" ry="72"/>
    </g>

    <g class="connectors">
      <line class="connector" x1="211" y1="185" x2="211" y2="272"/>
      <line class="connector" x1="584" y1="917" x2="643" y2="973"/>
    </g>

    <g class="hex-frames">
      <polygon class="hex-frame" points="211,272 330,341 330,479 211,548 92,479 92,341"/>
      <polygon class="hex-frame" points="338,489 457,558 457,696 338,765 219,696 219,558"/>
      <polygon class="hex-frame" points="590,489 709,558 709,696 590,765 471,696 471,558"/>
      <polygon class="hex-frame" points="464,708 583,777 583,915 464,984 345,915 345,777"/>
    </g>

    <g class="pillar pillar-agile">
      <text class="initial" x="211" y="428">A</text>
      <text class="keyword" x="209" y="480">Agile</text>
    </g>
    <g class="pillar pillar-boost">
      <text class="initial" x="348" y="646">B</text>
      <text class="keyword" x="340" y="697">Boost</text>
    </g>
    <g class="pillar pillar-customer">
      <text class="initial" x="591" y="646">C</text>
      <text class="keyword" x="598" y="697">Customer</text>
    </g>
    <g class="pillar pillar-data">
      <text class="initial" x="473" y="861">D</text>
      <text class="keyword" x="463" y="914">Data</text>
    </g>
  </svg>
</main>
</body>
</html>
```